Corvane Holdings , new business card design

investment firm with corporate clients . need double sided business card , vertical and horizontal options ,logo must be clear. prefer pantone colors only and sharp design. website also www.corvane.ae

Khalid Bin Tarrafi
Managing Director
Tel. +971 4 387 2940
Mobile +971 50 518 2403
khalid@corvane.ae
Q-Span Plaza, officw 18-B07, Warqa Gardens, Dubai

Contact Information for Business Card

Khalid Bin Tarrafi
Managing Director

Font styles to use
Serif

Colors

Designer to choose colors to be used in the design.

```html
<!DOCTYPE html>
<html lang="en">
<head>
<meta charset="utf-8">
<title>Corvane Holdings — Business Card</title>
<link rel="stylesheet" href="https://fonts.googleapis.com/css2?family=Lato:wght@300;400;700&display=swap">
<style>
  :root {
    --navy: #0b2466;
    --steel: #4e7196;
    --rule: #3d6a9a;
    --paper: #ffffff;
    --backdrop: #e9ebef;
    --ink-light: #ffffff;
  }
  * { margin: 0; padding: 0; box-sizing: border-box; }
  html, body {
    width: 1200px; height: 960px; overflow: hidden;
    background: var(--backdrop);
    font-family: "Lato", sans-serif;
  }
  .stage {
    position: relative; width: 1200px; height: 960px;
  }
  .card {
    position: absolute; left: 280px; width: 640px; height: 366px;
    overflow: hidden;
    box-shadow: 0 6px 18px rgba(20, 30, 60, 0.18);
  }
  /* Front side */
  .card-front {
    top: 90px; background: var(--navy); color: var(--ink-light);
    display: flex; flex-direction: column; align-items: center; justify-content: center;
  }
  .brand-name {
    font-family: "Lato", sans-serif;
    font-weight: 300;
    text-transform: uppercase;
    letter-spacing: 0.32em;
    white-space: nowrap;
  }
  .card-front .brand-name { font-size: 38px; color: var(--ink-light); margin-bottom: 34px; padding-left: 0.32em; }
  .website { font-size: 20px; letter-spacing: 0.16em; font-weight: 400; }

  /* Back side */
  .card-back { top: 516px; background: var(--paper); }
  .card-back .brand-name {
    position: absolute; top: 62px; left: 0; right: 0; text-align: center;
    font-size: 32px; color: var(--navy); padding-left: 0.32em;
  }
  .rule { position: absolute; left: 0; right: 0; height: 2px; background: var(--rule); }
  .rule-top { top: 140px; }
  .rule-bottom { top: 236px; }
  .person {
    position: absolute; top: 160px; left: 0; right: 0; text-align: center; color: var(--navy);
  }
  .person-name { font-weight: 700; font-size: 19px; letter-spacing: 0.03em; text-transform: uppercase; }
  .person-title { font-weight: 400; font-size: 18px; letter-spacing: 0.04em; text-transform: uppercase; margin-top: 2px; }

  .contact-band {
    position: absolute; left: 0; right: 0; top: 246px; bottom: 0;
    background: var(--navy); color: var(--ink-light);
    display: flex; justify-content: center; align-items: center;
    font-size: 15px; line-height: 1.65;
  }
  .address { text-align: right; padding-right: 16px; }
  .divider { width: 1px; align-self: stretch; margin: 24px 0; background: rgba(255,255,255,0.45); }
  .contacts { list-style: none; padding-left: 16px; }
  .contacts li { display: flex; align-items: center; gap: 7px; }
  .contacts svg { width: 13px; height: 13px; fill: var(--ink-light); flex: none; }
</style>
</head>
<body>
<main class="stage">
  <section class="card card-front" aria-label="Card front">
    <div class="brand-name">Corvane Holdings</div>
    <div class="website">www.corvane.ae</div>
  </section>

  <section class="card card-back" aria-label="Card back">
    <div class="brand-name">Corvane Holdings</div>
    <div class="rule rule-top"></div>
    <div class="person">
      <div class="person-name">Khalid Bin Tarrafi</div>
      <div class="person-title">Managing Director</div>
    </div>
    <div class="rule rule-bottom"></div>
    <div class="contact-band">
      <address class="address" style="font-style:normal">
        Q-Span Plaza<br>
        officw 18-B07<br>
        Warqa Gardens, Dubai
      </address>
      <div class="divider"></div>
      <ul class="contacts">
        <li>
          <svg viewBox="0 0 16 16" aria-hidden="true"><circle cx="8" cy="8" r="7.2" fill="none" stroke="#fff" stroke-width="1.4"/><path d="M5.2 4.2l1.6-.2.7 1.9-1 .8c.5 1.1 1.3 2 2.4 2.5l.8-1 1.9.7-.2 1.6c-3.4.2-6.4-2.8-6.2-6.3z"/></svg>
          +971 4 387 2940
        </li>
        <li>
          <svg viewBox="0 0 16 16" aria-hidden="true"><rect x="4" y="1" width="8" height="14" rx="1.5"/><rect x="5.3" y="3" width="5.4" height="7" fill="#0b2466"/><circle cx="8" cy="12.5" r="0.9" fill="#0b2466"/></svg>
          +971 50 518 2403
        </li>
        <li>
          <svg viewBox="0 0 16 16" aria-hidden="true"><rect x="1" y="3.5" width="14" height="9.5" rx="1"/><path d="M1.5 4l6.5 5 6.5-5" fill="none" stroke="#0b2466" stroke-width="1.3"/></svg>
          khalid@corvane.ae
        </li>
      </ul>
    </div>
  </section>
</main>
</body>
</html>
```